Business card for a Exhibition booth fabrication company

Hi. My company would like to change our corporate name card. We are an events and Exhibition stand builder company. We would like our corporate name card to resonate what we do. I need someone to create something unique that relates to the industry that I am in. The graphic designer should be creative to incorporate the elements of my industry and try to blend in well in the design of the card. Our aim is to ensure that we are unique and our card can look different from our competitors.
Updates

Target Market(s)

Marketing and events manager from all companies

Contact Information for Business Card

The business card should have the following details:
Name
Job Title
Email
Website

Colors

Designer to choose colors to be used in the design.

Requirements
Must have
• The card must be look something that is relevant to the service that I am providing. My website is: www.velmora-buildworks.com
• You can see my website to get more information on what service that I am doing
Nice to have
• On the back of my card, I would like to have a globe image with the incorporation of my company logo. This is to indicate that my services can be done in any part of the world.

```html
<!DOCTYPE html>
<html lang="en">
<head>
<meta charset="utf-8">
<title>Velmora Buildworks – Business Card</title>
<link rel="stylesheet" href="https://fonts.googleapis.com/css2?family=Open+Sans:wght@400;600;700&display=swap">
<style>
  :root {
    --page: #ecebe9;
    --card-white: #ffffff;
    --card-grey: #5c5c5e;
    --band-grey: #616164;
    --brand-red: #ec1c24;
    --text-grey: #6a6a6c;
    --text-dark: #333335;
    --map-tone: #686869;
  }
  * { box-sizing: border-box; margin: 0; padding: 0; }
  html, body { width: 1200px; height: 997px; overflow: hidden; }
  body {
    background: var(--page);
    font-family: "Open Sans", Arial, sans-serif;
    position: relative;
  }
  .card {
    position: absolute;
    left: 250px;
    width: 700px;
    height: 400px;
    border-radius: 4px;
    box-shadow: 0 6px 18px rgba(0,0,0,0.12);
    overflow: hidden;
  }
  .card--front { top: 66px; background: var(--card-white); }
  .card--back  { top: 530px; background: var(--card-grey); }

  /* front */
  .brand { position: absolute; display: flex; align-items: center; gap: 14px; }
  .brand__mark { width: 40px; height: 40px; border-radius: 50%; background: var(--brand-red); }
  .brand__name {
    font-weight: 700;
    letter-spacing: 3px;
    font-size: 22px;
  }
  .card--front .brand { left: 60px; top: 62px; }
  .card--front .brand__name { color: var(--text-grey); }

  .bands { position: absolute; inset: 0; }

  .contact { position: absolute; left: 60px; list-style: none; }
  .contact li { display: flex; align-items: center; gap: 8px; font-size: 15px; color: var(--text-dark); height: 24px; }
  .contact svg { width: 14px; height: 14px; flex: none; }
  .contact--plain { top: 176px; }
  .contact--plain li { border-left: 2px solid #b9b9bb; padding-left: 8px; }

  .band-line {
    position: absolute; left: 60px; display: flex; align-items: center; gap: 10px;
    color: #ffffff; font-size: 15px; height: 35px;
  }
  .band-line svg { width: 14px; height: 14px; }
  .band-line--email { top: 255px; }
  .band-line--web   { top: 290px; }

  .holder {
    position: absolute; left: 440px; top: 170px; width: 200px; height: 85px;
    display: flex; flex-direction: column; align-items: center; justify-content: center;
    color: #ffffff;
  }
  .holder__name { font-weight: 700; font-size: 16px; letter-spacing: 0.5px; text-transform: uppercase; }
  .holder__title { font-size: 14px; }

  /* back */
  .world-map {
    position: absolute; left: 70px; top: 30px; width: 560px; height: 340px;
    border-radius: 50%;
    background: radial-gradient(ellipse at center, var(--map-tone) 0%, rgba(104,104,105,0.45) 55%, rgba(92,92,94,0) 75%);
  }
  .card--back .brand {
    left: 0; right: 0; top: 170px; justify-content: center;
  }
  .card--back .brand__name { color: #ffffff; font-size: 26px; }
</style>
</head>
<body>

<section class="card card--front" aria-label="Card front">
  <svg class="bands" viewBox="0 0 700 400" aria-hidden="true">
    <rect x="600" y="178" width="100" height="20" fill="var(--band-grey)"/>
    <rect x="0" y="255" width="700" height="35" fill="var(--band-grey)"/>
    <rect x="0" y="290" width="700" height="35" fill="var(--brand-red)"/>
    <path d="M440 290 V184 Q440 170 454 170 H626 Q640 170 640 184 V255 Q640 290 670 290 Z" fill="var(--brand-red)"/>
  </svg>

  <div class="brand">
    <span class="brand__mark"></span>
    <span class="brand__name">VELMORA BUILDWORKS</span>
  </div>

  <ul class="contact contact--plain">
    <li>
      <svg viewBox="0 0 16 16"><path d="M4 1l3 3-2 2c1 2 3 4 5 5l2-2 3 3-2 3C7 15 1 9 1 3z" fill="var(--brand-red)"/></svg>
      +974 5550 2841
    </li>
    <li>
      <svg viewBox="0 0 16 16"><path d="M8 1a5 5 0 0 1 5 5c0 4-5 9-5 9S3 10 3 6a5 5 0 0 1 5-5z" fill="var(--brand-red)"/><circle cx="8" cy="6" r="2" fill="#fff"/></svg>
      P.O. Box 4120, Harbor Road, Doha - Qatar
    </li>
  </ul>

  <div class="band-line band-line--email">
    <svg viewBox="0 0 16 16"><rect x="1" y="3" width="14" height="10" rx="1" fill="#fff"/><path d="M1 4l7 5 7-5" stroke="var(--band-grey)" stroke-width="1.4" fill="none"/></svg>
    info@velmora-buildworks.com
  </div>
  <div class="band-line band-line--web">
    <svg viewBox="0 0 16 16" fill="none" stroke="#fff" stroke-width="1.3"><circle cx="8" cy="8" r="6.5"/><ellipse cx="8" cy="8" rx="3" ry="6.5"/><path d="M1.5 8h13"/></svg>
    www.velmora-buildworks.com
  </div>

  <div class="holder">
    <span class="holder__name">Daniel Reyes</span>
    <span class="holder__title">President</span>
  </div>
</section>

<section class="card card--back" aria-label="Card back">
  <div class="world-map" role="img" aria-label="Faint world map showing global reach"></div>
  <div class="brand">
    <span class="brand__mark"></span>
    <span class="brand__name">VELMORA BUILDWORKS</span>
  </div>
</section>

</body>
</html>
```